Motor Oil Lubricant Package Labels

We are looking for a logo and label that we can put on our motor oil bottle 1 liter and 5 liter. The name of our motor oil is Corvana. We want to design our flagship logo for CORVANA MOTOR OILS and as well as the label that will go on the bottle. We have some drafts that we have come up with attached and would like to see more options. The concept of a timeless motor oil and the endless loop of lubricating oils incorporated in the design. We will have full synthetic motor oil, a synthetic blend motor, ATF III transmission fluid, KRL-VI transmission fluid. hydraulic oils etc. Examples will be attached
Target Market(s)
Automotive Lubricants and Chemicals
Industry/Entity Type
Automotive
Logo Text
Corvana Lubricants
Font styles to use
Other font styles liked:
- Let designer choose
Requirements
Must have
- The Corvana sign incorporated in a very cool way to our name. Our brand needs to stick out
Nice to have
- Automotive lubricant related and colors red, white, and blue incorporated in the design
Should not have
- Images of individuals and or topics not related to automotive lubricants.

```html
<!DOCTYPE html>
<html lang="en">
<head>
<meta charset="utf-8">
<title>Corvana Motor Oil – 5W-30 Labels</title>
<link href="https://fonts.googleapis.com/css2?family=Oswald:wght@500;700&family=Exo+2:wght@800&family=Roboto+Condensed:wght@700&display=swap" rel="stylesheet">
<style>
  :root {
    --backdrop: #ebebeb;
    --gold-dark: #b8902f;
    --gold-mid: #d8b75a;
    --gold-light: #f1dc8e;
    --brand-red: #ec1c24;
    --brand-blue: #2d55a8;
    --ink: #2a2418;
    --white: #ffffff;
  }
  html, body {
    margin: 0;
    width: 1200px;
    height: 935px;
    overflow: hidden;
    background: radial-gradient(ellipse at center, #f6f6f6 0%, var(--backdrop) 75%);
    font-family: "Roboto Condensed", sans-serif;
  }
  .label {
    position: absolute;
    top: 120px;
    width: 434px;
    height: 702px;
    border-radius: 29px;
    overflow: hidden;
    background: linear-gradient(100deg, var(--gold-dark) 0%, var(--gold-light) 35%, var(--gold-mid) 60%, var(--gold-dark) 100%);
    box-shadow: 0 0 0 1px #c9c9c9;
  }
  .label--front { left: 132px; }
  .label--back { left: 618px; }
  .label__art { position: absolute; inset: 0; width: 100%; height: 100%; }

  .brand { position: absolute; left: 60px; top: 176px; }
  .label--back .brand { left: 64px; top: 168px; }
  .brand__name {
    font-family: "Exo 2", sans-serif;
    font-weight: 800;
    font-size: 50px;
    line-height: 1;
    color: var(--brand-blue);
    letter-spacing: -1px;
    display: flex;
    align-items: center;
    gap: 8px;
  }
  .brand__dot { width: 14px; height: 14px; border-radius: 50%; background: var(--brand-red); }
  .brand__line {
    font-family: "Exo 2", sans-serif;
    font-weight: 800;
    font-size: 14px;
    letter-spacing: 2px;
    color: var(--ink);
    text-align: right;
    margin-top: 6px;
  }

  .grade__sae {
    position: absolute; left: 306px; top: 288px;
    font-family: "Oswald", sans-serif; font-weight: 700;
    font-size: 32px; line-height: 1; color: var(--white);
  }
  .vertical { position: absolute; writing-mode: vertical-rl; color: var(--white); white-space: nowrap; }
  .grade__value {
    left: 300px; top: 322px;
    font-family: "Oswald", sans-serif; font-weight: 700;
    font-size: 104px; line-height: 0.78; letter-spacing: -2px;
  }
  .grade__type {
    left: 384px; top: 440px;
    font-family: "Oswald", sans-serif; font-weight: 500;
    font-size: 13px; letter-spacing: 1px; line-height: 1;
  }
  .grade__spec {
    left: 272px; top: 490px;
    font-family: "Oswald", sans-serif; font-weight: 700;
    font-size: 22px; line-height: 1;
  }

  .seal {
    position: absolute; left: 58px; top: 316px;
    width: 112px; height: 112px; border-radius: 50%;
    background: radial-gradient(circle, #f6e2a0 0%, var(--gold-dark) 100%);
    display: flex; align-items: center; justify-content: center;
  }
  .seal__inner {
    width: 78px; height: 78px; border-radius: 50%;
    background: var(--white);
    border: 4px solid #f7a823;
    display: flex; align-items: center; justify-content: center;
    text-align: center;
    font-size: 11px; line-height: 1.35; color: var(--ink);
  }

  .volume {
    position: absolute; left: 18px; top: 652px;
    font-size: 21px; color: var(--ink);
  }
  .origin {
    position: absolute; left: 187px; top: 650px;
    font-size: 17px; color: var(--white); text-align: center; line-height: 1;
  }
  .origin__stars { display: block; font-size: 8px; letter-spacing: 2px; margin-top: 2px; }

  .flag { position: absolute; left: 34px; top: 606px; width: 84px; }
  .flag svg { display: block; width: 84px; height: 46px; }
  .flag__caption {
    background: var(--white); color: #111;
    font-family: Arial, sans-serif; font-size: 10px; letter-spacing: 1.5px;
    text-align: center; padding: 1px 0;
  }
</style>
</head>
<body>

<section class="label label--front">
  <svg class="label__art" viewBox="0 0 543 878" preserveAspectRatio="none" aria-hidden="true">
    <path d="M110,0 L543,0 L543,110 C470,140 390,115 320,78 C240,36 170,10 110,0 Z" fill="var(--brand-red)"/>
    <path d="M295,0 L543,0 L543,85 C480,100 410,75 370,45 C340,22 312,8 295,0 Z" fill="var(--brand-blue)"/>
    <path d="M543,60 C500,180 430,270 395,320 C330,400 250,470 200,560 C160,640 160,740 215,810 C240,845 260,865 275,878 L543,878 Z" fill="var(--brand-red)"/>
    <path d="M543,70 C500,160 450,230 425,280 C380,350 300,420 250,520 C210,600 210,700 265,740 C300,780 380,810 543,835 Z" fill="var(--brand-blue)" stroke="var(--gold-light)" stroke-width="10"/>
  </svg>
  <div class="brand">
    <div class="brand__name"><span class="brand__dot"></span>CORVANA</div>
    <div class="brand__line">MOTOR OIL</div>
  </div>
  <div class="seal"><div class="seal__inner">FOR<br>GASOLINE<br>ENGIENS</div></div>
  <div class="grade__sae">SAE</div>
  <div class="vertical grade__value">5W-30</div>
  <div class="vertical grade__type">SYNTHETIC BLEND</div>
  <div class="vertical grade__spec">API SN</div>
  <div class="volume">32oz 1946mU</div>
  <div class="origin">Made In USA<span class="origin__stars">★★★</span></div>
</section>

<section class="label label--back">
  <svg class="label__art" viewBox="0 0 543 878" preserveAspectRatio="none" aria-hidden="true">
    <path d="M110,0 L543,0 L543,110 C470,140 390,115 320,78 C240,36 170,10 110,0 Z" fill="var(--brand-red)"/>
    <path d="M295,0 L543,0 L543,85 C480,100 410,75 370,45 C340,22 312,8 295,0 Z" fill="var(--brand-blue)"/>
    <path d="M543,60 C500,180 430,270 395,320 C330,400 250,470 200,560 C160,640 160,740 215,810 C240,845 260,865 275,878 L543,878 Z" fill="var(--brand-red)"/>
    <path d="M543,70 C500,160 450,230 425,280 C380,350 300,420 250,520 C210,600 210,700 265,740 C300,780 380,810 543,835 Z" fill="var(--brand-blue)" stroke="var(--gold-light)" stroke-width="10"/>
  </svg>
  <div class="brand">
    <div class="brand__name"><span class="brand__dot"></span>CORVANA</div>
    <div class="brand__line">MOTOR OIL</div>
  </div>
  <div class="grade__sae">SAE</div>
  <div class="vertical grade__value">5W-30</div>
  <div class="vertical grade__type">SYNTHETIC BLEND</div>
  <div class="vertical grade__spec">API SN</div>
  <div class="flag">
    <svg viewBox="0 0 84 46" role="img" aria-label="United States flag">
      <rect width="84" height="46" fill="#ffffff"/>
      <g fill="#c8102e">
        <rect y="0" width="84" height="3.54"/><rect y="7.08" width="84" height="3.54"/>
        <rect y="14.16" width="84" height="3.54"/><rect y="21.24" width="84" height="3.54"/>
        <rect y="28.32" width="84" height="3.54"/><rect y="35.4" width="84" height="3.54"/>
        <rect y="42.48" width="84" height="3.54"/>
      </g>
      <rect width="36" height="24.8" fill="#1f3a7a"/>
    </svg>
    <div class="flag__caption">MADE IN USA</div>
  </div>
</section>

</body>
</html>
```